Corvel's Auto Detailing is the company name. I will upload a picture that is something similar. However a few things will be different. I want my company name to be on it. And a picture of a nice car. As well as the packages offered. Also phone number which is 7264018835. Call or text. As far as the packages goes, I want the exact layout of the picture I uploaded. The only difference would be the prices. For full detail the price should be $149.99, engine detail is $39.99 headlight restoration is $19.99 exterior wash is $59.99 Interior is $59.99. Please make it pretty. I would like to see a copy before printing

Industry/Entity Type

It Company

```html
<!DOCTYPE html>
<html lang="en">
<head>
<meta charset="utf-8">
<title>Corvel's Auto Detailing – Service Packages</title>
<link href="https://fonts.googleapis.com/css2?family=Anton&family=Open+Sans:wght@600;700&display=swap" rel="stylesheet">
<style>
  :root {
    --page-bg: #e9e6e1;
    --flyer-dark: #2a2b2e;
    --brand-blue: #0a56a6;
    --brand-yellow: #fff200;
    --price-red: #e3161d;
    --tab-light: #f2f2f2;
    --tab-mid: #c9c9c9;
    --text-light: #ffffff;
    --text-dark: #222222;
  }
  * { margin: 0; padding: 0; box-sizing: border-box; }
  html, body {
    width: 1200px; height: 960px; overflow: hidden;
    background: var(--page-bg);
  }
  .flyer {
    position: absolute; left: 0; top: 80px;
    width: 1200px; height: 800px;
    background: var(--flyer-dark);
    overflow: hidden;
    font-family: "Open Sans", Arial, sans-serif;
  }
  .car-photo {
    position: absolute; inset: 88px 0 0 0;
    background:
      radial-gradient(ellipse 55% 45% at 55% 45%, rgba(200,200,200,.45), rgba(200,200,200,0) 70%),
      radial-gradient(ellipse 30% 30% at 85% 35%, rgba(180,180,180,.3), rgba(180,180,180,0) 70%),
      linear-gradient(180deg, #3a3b3e 0%, #4a4b4e 45%, #2e2f31 75%, #1f2022 100%);
  }
  .header-art { position: absolute; left: 0; top: 0; width: 1200px; height: 88px; }
  .brand-name {
    position: absolute; left: 0; top: 4px; width: 1200px; text-align: center;
    font-family: "Anton", Impact, sans-serif; font-size: 58px; line-height: 76px;
    color: var(--brand-yellow); letter-spacing: .5px;
  }
  .pkg-head { position: absolute; height: 66px; }
  .pkg-bar {
    position: absolute; left: 0; top: 6px; bottom: 6px; right: 60px;
    background: linear-gradient(180deg, var(--tab-light) 0%, #e2e2e2 55%, var(--tab-mid) 100%);
    clip-path: polygon(22px 0, 100% 0, 100% 100%, 0 100%);
    display: flex; align-items: center; padding-left: 32px;
  }
  .pkg-title {
    font-family: "Anton", Impact, sans-serif; color: var(--brand-blue);
    font-size: 42px; line-height: 1; white-space: nowrap; letter-spacing: .3px;
  }
  .pkg-title.small { font-size: 24px; }
  .price-tag {
    position: absolute; right: 0; top: 0; width: 110px; height: 66px;
    background: linear-gradient(180deg, #ffffff 0%, #e4e4e4 60%, #c6c6c6 100%);
    border-radius: 6px; text-align: center; color: var(--text-dark);
    padding-top: 3px;
  }
  .price-tag .from { font-size: 12px; font-weight: 600; line-height: 14px; display: block; }
  .price-tag .amount {
    font-family: "Anton", Impact, sans-serif; font-size: 28px; line-height: 32px;
    color: var(--price-red); display: block;
  }
  .price-tag .tax { font-size: 12px; font-weight: 600; line-height: 13px; display: block; }
  .service-list { position: absolute; list-style: none; color: var(--text-light); }
  .service-list li {
    position: relative; padding-left: 33px;
    font-size: 15.5px; font-weight: 600; line-height: 19px;
    text-transform: uppercase; white-space: nowrap; margin-bottom: 6.5px;
  }
  .service-list.roomy li { margin-bottom: 8px; }
  .service-list li::before {
    content: ""; position: absolute; left: 6px; top: 3px;
    width: 13px; height: 13px; border-radius: 50%;
    background: radial-gradient(circle, var(--flyer-dark) 0 2px, var(--brand-yellow) 2.5px 4px, #b8ad00 4.5px 5px, var(--brand-yellow) 5.5px);
  }
  .phone {
    position: absolute; left: 53px; top: 704px;
    font-family: "Open Sans", Arial, sans-serif; font-weight: 700;
    font-size: 58px; line-height: 62px; color: var(--brand-yellow); letter-spacing: -1px;
  }
  .phone-note {
    position: absolute; left: 53px; top: 766px; width: 386px; height: 21px;
    background: var(--brand-blue); color: var(--text-light);
    font-size: 14.5px; font-weight: 700; line-height: 21px; padding-left: 15px;
    white-space: nowrap;
  }
  .footer-band { position: absolute; left: 674px; top: 743px; width: 526px; height: 57px; }
  .footer-note {
    position: absolute; left: 732px; top: 743px; height: 57px;
    font-family: "Anton", Impact, sans-serif; font-size: 20px; line-height: 57px;
    color: var(--brand-yellow); letter-spacing: .3px; white-space: nowrap;
  }
</style>
</head>
<body>
<main class="flyer">
  <div class="car-photo" role="img" aria-label="Black and white photo of a white sports car with racing stripes"></div>

  <svg class="header-art" viewBox="0 0 1200 88" aria-hidden="true">
    <rect width="1200" height="88" fill="#1e1f21"/>
    <polygon points="132,0 1084,0 1046,88 132,88 170,0" fill="#0a56a6"/>
    <polygon points="132,0 170,0 132,88 94,88" fill="#0a56a6"/>
    <polygon points="40,0 75,0 37,88 11,88 11,80" fill="#fff200"/>
    <polygon points="100,0 139,0 101,88 62,88" fill="#fff200"/>
    <polygon points="1108,0 1146,0 1108,88 1070,88" fill="#fff200"/>
    <polygon points="1164,0 1200,0 1200,12 1168,88 1130,88" fill="#fff200"/>
  </svg>
  <h1 class="brand-name">Corvel's Auto Detailing</h1>

  <!-- Full detail -->
  <div class="pkg-head" style="left:56px; top:105px; width:375px;">
    <div class="pkg-bar"><span class="pkg-title">FULL DETAIL</span></div>
    <div class="price-tag"><span class="from">STARTING AT</span><span class="amount">$149.99</span><span class="tax">+ TAX</span></div>
  </div>
  <ul class="service-list" style="left:56px; top:195px;">
    <li>Wash car &amp; dry with microfiber towels</li>
    <li>Clean wheels &amp; wheel wells</li>
    <li>Clean all windows &amp; mirrors</li>
    <li>Vacuum carpets &amp; mats</li>
    <li>Wipe door jams apply tire dressing</li>
    <li>Apply polish for shine &amp; to remove minor scratches</li>
    <li>Apply premium wax to protect the clear coat</li>
    <li>Vacuum interior &amp; trunk shampoo carpets,<br>floor mats, seats</li>
    <li>Deep clean upholstery &amp; leather</li>
    <li>Apply conditioner to leather seats</li>
    <li>Clean all windows &amp; mirrors</li>
  </ul>

  <!-- Engine detail -->
  <div class="pkg-head" style="left:56px; top:489px; width:375px;">
    <div class="pkg-bar"><span class="pkg-title">ENGINE DETAIL</span></div>
    <div class="price-tag"><span class="from">STARTING AT</span><span class="amount">$39.99</span><span class="tax">+ TAX</span></div>
  </div>
  <ul class="service-list" style="left:56px; top:571px;">
    <li>Degrease engine, apply dressing</li>
    <li>To engine, clean hood compartment</li>
  </ul>

  <!-- Headlight restoration -->
  <div class="pkg-head" style="left:56px; top:628px; width:375px;">
    <div class="pkg-bar"><span class="pkg-title small">HEADLIGHT Restoration</span></div>
    <div class="price-tag"><span class="from">STARTING AT</span><span class="amount">$19.99</span><span class="tax">+ TAX</span></div>
  </div>

  <div class="phone">7264018835</div>
  <div class="phone-note">CALL OR TEXT. AS FAR AS THE PACKAGES GOES</div>

  <!-- Exterior detail -->
  <div class="pkg-head" style="left:699px; top:105px; width:448px;">
    <div class="pkg-bar"><span class="pkg-title">EXTERIOR DETAIL</span></div>
    <div class="price-tag"><span class="from">STARTING AT</span><span class="amount">$59.99</span><span class="tax">+ TAX</span></div>
  </div>
  <ul class="service-list roomy" style="left:699px; top:195px;">
    <li>Wash car &amp; dry with microfiber towels</li>
    <li>Clean wheels &amp; wheel wells</li>
    <li>Clean all windows &amp; mirrors</li>
    <li>Vacuum carpets &amp; mats</li>
    <li>Wipe door jams</li>
    <li>Apply tire dressing</li>
    <li>Apply polish for shine &amp; to remove<br>minor scratches</li>
    <li>Apply premium wax to protect clear coat.</li>
  </ul>

  <!-- Interior detail -->
  <div class="pkg-head" style="left:699px; top:466px; width:448px;">
    <div class="pkg-bar"><span class="pkg-title">INTERIOR DETAIL</span></div>
    <div class="price-tag"><span class="from">STARTING AT</span><span class="amount">$59.99</span><span class="tax">+ TAX</span></div>
  </div>
  <ul class="service-list roomy" style="left:699px; top:553px;">
    <li>Wash car &amp; dry with microfiber towels</li>
    <li>Vacuum interior &amp; trunk</li>
    <li>Shampoo carpets, floor mats, seats</li>
    <li>Deep clean upholstery &amp; leather</li>
    <li>Apply conditioner to leather seats</li>
    <li>Clean all windows &amp; mirrors</li>
  </ul>

  <svg class="footer-band" viewBox="0 0 526 57" aria-hidden="true">
    <polygon points="28,0 526,0 526,57 0,57" fill="#0a56a6"/>
  </svg>
  <div class="footer-note">ADDITIONAL CHARGES APPLY FOR LARGER VEHICLES</div>
</main>
</body>
</html>
```